Business card design for modern PanoWalk agency

Hello,

I need a business card design for my company Kites7Market.
We mainly offer Zorvex PanoWalk Tours (360° Photography) and it should be a business card with following details:

Name: Tobias Wendler
Number: +49 176 58 20 917
Mail: tobias@kites7market.com
website: kites7market.com

Main colour that we use is the red of the logo.
It´s also important to integrate the "Zorvex Verified logo" as the person on this business card is a Zorvex verified photographer.

And if possible we would also like to integrate something like send us a sms or Chatlo and we call you back. As the number is german but we sell now in Vienna, Austria.

We offer a good price but very high photography quality, as we are mostly students - that´s our concept.

Maybe an idea is to integrate something 360° on the back-side of the card, for example the photo attached (just an idea) or some great design.
See flyer (attached) and kites7market.com for inspiration, maybe use of the photo of me (attached) in a circle or something

I´m very excited for your designs and thanks a lot in advance!! :)

Target Market(s)

Shops, hotels, shopping centers, etc. in Vienna, Austria

Industry/Entity Type

Business

Contact Information for Business Card

double-sided, use red of the logo, 360° zorvex pano walk certified photographer

Font styles to use
Serif
Sans Serif

Colors
ec1f27

Requirements
Nice to have
• maybe some 360° design on back-side
• maybe include photo of me in a circle or something or sketched in red colour

```html
<!DOCTYPE html>
<html lang="en">
<head>
<meta charset="utf-8">
<title>Kites7Market business card</title>
<link rel="stylesheet" href="https://fonts.googleapis.com/css2?family=Open+Sans:wght@400;600;700&display=swap">
<style>
  :root {
    --brand-red: #ec1f27;
    --ink: #2a2a2a;
    --grey: #9a9a9a;
    --paper: #ffffff;
    --backdrop: #e9e7e5;
    --faint: rgba(0, 0, 0, 0.035);
    --photo-warm: #d9c29a;
    --photo-haze: #bfae8e;
    --photo-road: #7a6d5e;
  }
  * { box-sizing: border-box; margin: 0; padding: 0; }
  html, body {
    width: 1200px; height: 844px; overflow: hidden;
    background: var(--backdrop);
    font-family: "Open Sans", Arial, sans-serif;
  }
  .canvas {
    position: relative; width: 1200px; height: 844px;
    display: flex; align-items: center; justify-content: center; gap: 44px;
  }
  .card {
    position: relative; width: 520px; height: 306px;
    background: var(--paper); overflow: hidden;
    box-shadow: 0 2px 10px rgba(0, 0, 0, 0.12);
  }

  /* ---- contact side ---- */
  .faint-mark {
    position: absolute; left: 28px; top: 30px;
    width: 120px; height: 120px;
    background: var(--faint);
  }
  .brand {
    position: absolute; display: flex; align-items: center; gap: 10px;
  }
  .brand-square { width: 56px; height: 56px; background: var(--brand-red); flex: none; }
  .brand-name {
    font-weight: 700; font-size: 30px; letter-spacing: -0.5px; line-height: 1;
    white-space: nowrap;
  }
  .card-contact .brand { left: 220px; top: 46px; }
  .card-contact .brand-name { color: var(--grey); }

  .person { position: absolute; left: 40px; top: 178px; }
  .person-name {
    color: var(--brand-red); font-weight: 700; font-size: 15px;
    letter-spacing: 0.3px; line-height: 20px; margin-bottom: 3px;
  }
  .contact-list { list-style: none; }
  .contact-list li {
    display: flex; align-items: center; gap: 8px;
    font-size: 12.5px; color: var(--ink); line-height: 18px;
  }
  .contact-list svg { width: 10px; height: 10px; flex: none; }
  .callback {
    margin-top: 10px; color: var(--brand-red);
    font-weight: 600; font-size: 14.5px; white-space: nowrap;
  }

  /* ---- brand side ---- */
  .photo {
    position: absolute; left: 0; top: 0; width: 520px; height: 212px;
    background: linear-gradient(100deg, var(--photo-warm) 0%, var(--photo-haze) 45%, var(--photo-road) 100%);
  }
  .card-photo .brand { left: 110px; top: 74px; }
  .card-photo .brand-square { width: 70px; height: 70px; }
  .card-photo .brand-name { color: var(--ink); font-size: 36px; }
  .verified {
    position: absolute; left: 0; right: 0; top: 226px;
    display: flex; align-items: center; justify-content: center; gap: 7px;
    font-size: 15px; font-weight: 600; color: var(--ink); line-height: 22px;
  }
  .verified-dot {
    width: 12px; height: 12px; border-radius: 50%; background: var(--brand-red); flex: none;
  }
</style>
</head>
<body>
<main class="canvas">

  <section class="card card-contact" aria-label="Contact side">
    <div class="faint-mark" aria-hidden="true"></div>
    <div class="brand">
      <span class="brand-square" aria-hidden="true"></span>
      <span class="brand-name">Kites7Market</span>
    </div>
    <div class="person">
      <h1 class="person-name">TOBIAS WENDLER</h1>
      <ul class="contact-list">
        <li>
          <svg viewBox="0 0 10 10" aria-hidden="true"><path fill="#ec1f27" d="M2 0.5 3.6 2.6 2.8 3.7Q4 6 6.3 7.2L7.4 6.4 9.5 8 8.3 9.5Q4 9 0.5 1.7Z"/></svg>
          +49 176 58 20 917
        </li>
        <li>
          <svg viewBox="0 0 10 10" aria-hidden="true"><rect x="0.5" y="2" width="9" height="6.5" fill="#ec1f27"/><path d="M0.8 2.3 5 5.6 9.2 2.3" stroke="#fff" stroke-width="0.9" fill="none"/></svg>
          tobias@kites7market.com
        </li>
        <li>
          <svg viewBox="0 0 10 10" aria-hidden="true"><circle cx="5" cy="5" r="4.5" fill="#ec1f27"/><path d="M0.5 5H9.5M5 0.5C2.8 3 2.8 7 5 9.5M5 0.5C7.2 3 7.2 7 5 9.5" stroke="#fff" stroke-width="0.7" fill="none"/></svg>
          www.kites7market.com
        </li>
      </ul>
      <p class="callback">Send us a sms or Chatlo and we call you back</p>
    </div>
  </section>

  <section class="card card-photo" aria-label="Brand side">
    <div class="photo" role="img" aria-label="Photo of a runner's legs on a sunlit city street with tall buildings in a warm haze"></div>
    <div class="brand">
      <span class="brand-square" aria-hidden="true"></span>
      <span class="brand-name">Kites7Market</span>
    </div>
    <p class="verified">
      <span class="verified-dot" aria-hidden="true"></span>
      Zorvex PanoWalk verified
    </p>
  </section>

</main>
</body>
</html>
```